Sales Deck Redesign for a B2B business selling customer service AI products

We are looking for a redesign of our sales Deck. we are a B2B business selling customer service AI products.

The sales deck is attached, we would like this to be made less "powerpoint" and more "professional expertise in a friendly package".

Our brand standards are attached with details on logos, colours and imagery.

Other examples of inspiration:
-Our website: https://www.ol-tiva.co.uk/
-Brindlecrest imagery - we are a Brindlecrest partner, so linking imagery with Brindlecrest would help.
-Competitor: https://www.morventapp.com/
-Ol-tiva Pulsecheck landing page: https://ol-tiva.tallyhive.com/

Full image files and AI/PNG files available on request

Slide 17 is a very rough design but if you can create something that is in line with the rest of the deck that would be great

Target Market(s)

Customer service teams and contact centres

Industry/Entity Type

Technology - Brindlecrest Ecosystem

Colors
0054AA
0677BA
7BADD7
CADEEF
E8F1F8

Requirements
Must have
• See description and branding doc
Nice to have
Should not have

```html
<!DOCTYPE html>
<html lang="en">
<head>
<meta charset="utf-8">
<title>Ol-tiva AI Sales Deck</title>
<link href="https://fonts.googleapis.com/css2?family=Barlow+Condensed:wght@600;700&family=Arimo:wght@400;700&family=Montserrat:wght@800&display=swap" rel="stylesheet">
<style>
:root{
  --navy:#231f6e;
  --blue:#0677ba;
  --bright:#1a8fd6;
  --deep:#0054aa;
  --sky:#7badd7;
  --pale:#cadeef;
  --mist:#e8f1f8;
  --orange:#f58220;
  --ink:#1b1b1b;
  --grey:#b3b3b3;
  --board:#9a9a9a;
}
*{margin:0;padding:0;box-sizing:border-box}
html,body{width:1200px;height:998px;overflow:hidden}
body{background:var(--board);font-family:"Arimo",Arial,sans-serif;color:var(--ink);position:relative}
.slide{position:absolute;width:471px;height:265px;background:#fff;overflow:hidden;box-shadow:0 10px 24px rgba(0,0,0,.35)}
.s-cover{left:119px;top:87px}
.s-problem{left:610px;top:87px}
.s-about{left:119px;top:367px}
.s-impact{left:610px;top:367px}
.s-why{left:119px;top:646px;background:linear-gradient(135deg,#1b2a6e,#152057 60%,#1d2f7a)}
.s-close{left:610px;top:646px;background:linear-gradient(120deg,#2a1f7a,#1a1650 55%,#120f3a)}
.abs{position:absolute}
.head{font-family:"Barlow Condensed","Arial Narrow",sans-serif;font-weight:700;text-transform:uppercase;line-height:1.1}
.head .hl{color:var(--blue)}
.brand{position:absolute;display:flex;align-items:center;gap:4px;font-family:"Barlow Condensed","Arial Narrow",sans-serif;font-weight:700;color:var(--deep);letter-spacing:1px;text-transform:uppercase}
.brand .dot{width:10px;height:10px;border-radius:50%;border:1.5px solid var(--deep)}
.brand.light{color:#fff}
.brand.light .dot{border-color:#fff}
.pageno{position:absolute;right:10px;bottom:9px;width:13px;height:13px;border-radius:50%;background:var(--blue);color:#fff;font-size:4.5px;font-weight:700;display:flex;align-items:center;justify-content:center}
.art{position:absolute}
.robot{background:radial-gradient(closest-side,#5fc6f2,#1b8fd3 65%,rgba(27,143,211,0))}
.hill{position:absolute;border-radius:50%;background:var(--navy)}
.ring{position:absolute}
/* cover */
.s-cover .title{left:24px;top:116px;width:190px;text-align:center;font-size:17px}
.s-cover .lede{left:45px;top:168px;width:148px;text-align:center;font-size:7.2px;line-height:1.45}
.badge{position:absolute;left:250px;top:56px;width:64px;height:68px;border-radius:4px;background:var(--navy)}
/* problem */
.s-problem .title{left:27px;top:20px;font-size:17px}
.issue{position:absolute;font-size:7.3px;line-height:1.5;width:120px}
.issue.left{text-align:right;left:8px}
.issue.right{left:339px}
.xmark{position:absolute;width:12px;height:12px}
/* about */
.s-about .title{left:28px;top:20px;font-size:17px}
.facts{position:absolute;left:28px;top:48px;list-style:none;font-size:7.4px;line-height:2}
.facts li::before{content:"";display:inline-block;width:3px;height:3px;border-radius:50%;background:var(--blue);margin:0 9px 1px 1px;vertical-align:middle}
.stat-big{position:absolute;font-family:"Montserrat",sans-serif;font-weight:800;font-size:15px}
.stat-copy{position:absolute;font-size:13.5px;line-height:1.3;color:#333}
.clients{position:absolute;left:28px;top:186px;width:305px;display:flex;justify-content:space-between;font-weight:700;font-size:10px;color:#333}
.divider{position:absolute;left:0;top:168px;width:330px;height:1px;background:#e4e4e4}
.band{position:absolute;left:0;top:234px;width:360px;height:40px;background:var(--bright);border-radius:60% 0 0 0/22% 0 0 0;color:#fff;font-family:"Barlow Condensed",sans-serif;font-weight:600;font-size:15.5px;text-align:center;padding-top:8px;padding-right:10px}
/* impact */
.s-impact .title{left:27px;top:20px;font-size:17px}
.metric{position:absolute;width:140px;text-align:center}
.metric .num{font-family:"Montserrat",sans-serif;font-weight:800;font-size:19px;color:var(--ink)}
.metric .desc{font-size:11px;line-height:1.3;color:#333;margin-top:4px}
/* why */
.s-why .title{left:266px;top:148px;font-size:22px;color:#fff;line-height:1.2}
.s-why .title .hl{color:var(--orange)}
/* close */
.disc{position:absolute;left:33px;top:32px;width:196px;height:196px;border-radius:50%;background:#fff}
.s-close .title{left:33px;top:87px;width:196px;text-align:center;font-size:15px;color:var(--navy);line-height:1.36}
.s-close .title .hl{color:var(--bright)}
.pairing{position:absolute;left:33px;top:166px;width:196px;display:flex;justify-content:center;align-items:center;gap:7px}
.pairing .plus{font-weight:700;font-size:10px}
.partner{font-family:"Barlow Condensed",sans-serif;font-weight:700;font-size:8px;color:#fff;background:var(--bright);border-radius:9px;padding:3px 6px}
</style>
</head>
<body>

<section class="slide s-cover">
  <svg class="ring" width="230" height="230" style="left:4px;top:18px" viewBox="0 0 230 230">
    <circle cx="115" cy="115" r="102" fill="#fff" stroke="var(--navy)" stroke-width="7"/>
    <path d="M13 115 A102 102 0 0 1 140 16" fill="none" stroke="var(--bright)" stroke-width="7"/>
  </svg>
  <div class="brand" style="left:64px;top:82px;font-size:11px"><span class="dot"></span>Ol-tiva AI</div>
  <h1 class="head abs title"><span class="hl">Automated Quality</span><br>Assurance A.I</h1>
  <p class="abs lede">Automate your Quality Assurance and improve your insight by 50x</p>
  <div class="badge" aria-hidden="true"></div>
  <div class="hill" style="left:340px;top:187px;width:220px;height:220px"></div>
  <div class="art robot" role="img" aria-label="Friendly blue assistant robot mascot waving" style="left:330px;top:20px;width:135px;height:200px"></div>
  <span class="pageno">01</span>
</section>

<section class="slide s-problem">
  <div class="brand" style="right:16px;top:12px;font-size:9px"><span class="dot"></span>Ol-tiva AI</div>
  <h2 class="head abs title"><span class="hl">Manual QA lacks insight</span><br>&amp; wastes resources</h2>
  <svg class="ring" width="160" height="160" style="left:155px;top:79px" viewBox="0 0 160 160">
    <circle cx="80" cy="80" r="74" fill="none" stroke="var(--navy)" stroke-width="4"/>
    <path d="M6 80 A74 74 0 0 1 80 6" fill="none" stroke="var(--bright)" stroke-width="4"/>
  </svg>
  <div class="art robot" role="img" aria-label="Small worried robot mascot" style="left:205px;top:108px;width:60px;height:100px"></div>
  <p class="issue left" style="top:96px">On average, only 2% of all cases will be audited</p>
  <p class="issue left" style="top:148px">Cases are randomly selected, meaning issues can be missed</p>
  <p class="issue left" style="top:200px">Compliance and soft skill risks are only found on randomly selected cases, not the other 98%</p>
  <p class="issue right" style="top:96px">QA tools are not integrated, or worse... on spreadsheets!</p>
  <p class="issue right" style="top:148px">Reporting is delayed, with no key reporting/dashboards</p>
  <p class="issue right" style="top:200px">Feedback training cycles are slow and lack impact</p>
  <svg class="xmark" style="left:137px;top:101px" viewBox="0 0 12 12"><circle cx="6" cy="6" r="5" fill="none" stroke="var(--orange)" stroke-width="1.2"/><path d="M4 4l4 4M8 4l-4 4" stroke="var(--orange)" stroke-width="1.2"/></svg>
  <svg class="xmark" style="left:137px;top:153px" viewBox="0 0 12 12"><circle cx="6" cy="6" r="5" fill="none" stroke="var(--orange)" stroke-width="1.2"/><path d="M4 4l4 4M8 4l-4 4" stroke="var(--orange)" stroke-width="1.2"/></svg>
  <svg class="xmark" style="left:137px;top:205px" viewBox="0 0 12 12"><circle cx="6" cy="6" r="5" fill="none" stroke="var(--orange)" stroke-width="1.2"/><path d="M4 4l4 4M8 4l-4 4" stroke="var(--orange)" stroke-width="1.2"/></svg>
  <svg class="xmark" style="left:318px;top:101px" viewBox="0 0 12 12"><circle cx="6" cy="6" r="5" fill="none" stroke="var(--orange)" stroke-width="1.2"/><path d="M4 4l4 4M8 4l-4 4" stroke="var(--orange)" stroke-width="1.2"/></svg>
  <svg class="xmark" style="left:318px;top:153px" viewBox="0 0 12 12"><circle cx="6" cy="6" r="5" fill="none" stroke="var(--orange)" stroke-width="1.2"/><path d="M4 4l4 4M8 4l-4 4" stroke="var(--orange)" stroke-width="1.2"/></svg>
  <svg class="xmark" style="left:318px;top:205px" viewBox="0 0 12 12"><circle cx="6" cy="6" r="5" fill="none" stroke="var(--orange)" stroke-width="1.2"/><path d="M4 4l4 4M8 4l-4 4" stroke="var(--orange)" stroke-width="1.2"/></svg>
  <span class="pageno">04</span>
</section>

<section class="slide s-about">
  <div class="brand" style="right:16px;top:12px;font-size:9px"><span class="dot"></span>Ol-tiva AI</div>
  <h2 class="head abs title"><span class="hl">A bit</span> about us</h2>
  <ul class="facts">
    <li>Trusted by companies across the globe to transform their customer service</li>
    <li>Founded by contact centre leaders in 2015</li>
    <li>Brindlecrest Partnerhub Partner 5 Star-rated listing</li>
  </ul>
  <div class="stat-big" style="left:28px;top:103px;color:var(--orange)">100m+</div>
  <p class="stat-copy" style="left:28px;top:122px">AI predictions provided<br>so far by</p>
  <div class="stat-big" style="left:206px;top:103px;color:var(--bright)">NOVA</div>
  <p class="stat-copy" style="left:206px;top:122px">Our AI Assistant!</p>
  <div class="divider"></div>
  <div class="clients"><span>Pinecrest</span><span>Harlowe</span><span>Fernbrook</span><span>pennynest</span><span>Quantaro</span></div>
  <div class="hill" style="left:340px;top:187px;width:220px;height:220px"></div>
  <div class="band">We take Complexity and bring Clarity</div>
  <div class="art robot" role="img" aria-label="Cheerful blue assistant robot mascot with raised arms" style="left:348px;top:50px;width:115px;height:185px"></div>
  <span class="pageno">02</span>
</section>

<section class="slide s-impact">
  <div class="brand" style="right:16px;top:12px;font-size:9px"><span class="dot"></span>Ol-tiva AI</div>
  <h2 class="head abs title"><span class="hl">Resulting in a lower NPS score,</span><br>wasted time &amp; risk</h2>
  <svg class="ring" width="471" height="160" style="left:0;top:80px" viewBox="0 0 471 160">
    <g fill="none" stroke-width="4">
      <circle cx="85" cy="73" r="70" stroke="var(--grey)"/>
      <path d="M15 73 A70 70 0 0 1 85 3" stroke="var(--bright)"/>
      <circle cx="235" cy="73" r="70" stroke="var(--grey)"/>
      <path d="M165 73 A70 70 0 0 1 235 3" stroke="var(--orange)"/>
      <circle cx="386" cy="73" r="70" stroke="var(--grey)"/>
      <path d="M316 73 A70 70 0 0 1 386 3" stroke="var(--bright)"/>
    </g>
  </svg>
  <div class="metric" style="left:15px;top:117px"><div class="num">98%</div><div class="desc">of service cases<br>missed every day</div></div>
  <div class="metric" style="left:165px;top:117px"><div class="num">3 Months+</div><div class="desc">delay in QA training<br>for agents</div></div>
  <div class="metric" style="left:316px;top:117px"><div class="num">£46k+</div><div class="desc">of wasted spend due<br>to manual effort*</div></div>
  <div class="art robot" role="img" aria-label="Robot mascot peeking up from the bottom edge" style="left:122px;top:216px;width:72px;height:60px"></div>
  <span class="pageno">05</span>
</section>

<section class="slide s-why">
  <div class="art" role="img" aria-label="Glowing blue digital globe of connected data points" style="left:20px;top:20px;width:250px;height:240px;background:radial-gradient(closest-side,#3a7be0 0%,#2456b8 45%,rgba(30,60,150,.4) 75%,rgba(27,42,110,0))"></div>
  <div class="brand light" style="right:10px;top:20px;font-size:11px"><span class="dot"></span>Ol-tiva AI</div>
  <h2 class="head abs title">Why you need<br><span class="hl">AI-powered</span> quality<br>assurance</h2>
  <span class="pageno">03</span>
</section>

<section class="slide s-close">
  <div class="art" role="img" aria-label="Deep purple starfield with glowing network of points" style="left:200px;top:0;width:271px;height:265px;background:radial-gradient(closest-side,rgba(90,90,200,.45),rgba(20,15,60,0))"></div>
  <svg class="ring" width="212" height="212" style="left:25px;top:24px" viewBox="0 0 212 212">
    <circle cx="106" cy="106" r="101" fill="none" stroke="var(--navy)" stroke-width="6"/>
    <path d="M5 106 A101 101 0 0 1 130 8" fill="none" stroke="var(--bright)" stroke-width="6"/>
  </svg>
  <div class="disc"></div>
  <h2 class="head abs title"><span class="hl">We’re supercharging</span><br>quality assurance for<br><span class="hl">Brindlecrest users</span></h2>
  <div class="pairing">
    <div class="brand" style="position:static;font-size:8px"><span class="dot" style="width:8px;height:8px"></span>Ol-tiva AI</div>
    <span class="plus">+</span>
    <span class="partner">Brindlecrest</span>
  </div>
  <span class="pageno">06</span>
</section>

</body>
</html>
```